RW Framewell Inc Business cards

We need business cards using our existing logo but slightly modified. Right now the logo says RW Loadbearing Masonry. We want to keep the RW part of the design, but replace the Structural Concrete portion with "FRAMEWELL". Please see the attached file.
Ideally this would be a blank template so we can add Different Names, titles, and phone numbers later.
On the one side we want only the logo and on the other side the detail. I'm attaching an example for you to see.
Please reach out with any other questions. Our address and other details will be given out once we find a design we like.

Target Market(s)

Construction Industry

```html
<!DOCTYPE html>
<html lang="en">
<head>
<meta charset="utf-8">
<title>RW Framewell Inc – Business Cards</title>
<link rel="stylesheet" href="https://fonts.googleapis.com/css2?family=Montserrat:wght@400;500;700&display=swap">
<style>
  :root {
    --backdrop: #3b3b3d;
    --card: #141416;
    --card-edge: #1d1d20;
    --brand-blue: #2f6fd1;
    --text-light: #ffffff;
    --text-muted: #c9ccd2;
  }
  * { box-sizing: border-box; margin: 0; padding: 0; }
  html, body { width: 800px; height: 1200px; overflow: hidden; }
  body {
    background: var(--backdrop);
    font-family: "Montserrat", Arial, sans-serif;
    color: var(--text-light);
    position: relative;
  }
  .card {
    position: absolute;
    left: 60px;
    width: 680px;
    height: 390px;
    background: var(--card);
    border: 1px solid var(--card-edge);
    overflow: hidden;
  }
  .card--front { top: 150px; }
  .card--back { top: 660px; }

  .wordmark {
    display: flex;
    flex-direction: column;
    align-items: center;
    color: var(--text-light);
    font-weight: 700;
    line-height: 1;
  }
  .wordmark__initials { font-size: 110px; letter-spacing: 4px; }
  .wordmark__name { font-size: 40px; letter-spacing: 6px; margin-top: 8px; }
  .card--front .wordmark {
    position: absolute; left: 0; right: 0; top: 100px;
  }
  .card--back .wordmark {
    position: absolute; right: 50px; top: 120px;
  }
  .card--back .wordmark__initials { font-size: 72px; }
  .card--back .wordmark__name { font-size: 26px; letter-spacing: 4px; margin-top: 6px; }

  .person { position: absolute; left: 40px; top: 40px; }
  .person__name { color: var(--brand-blue); font-size: 24px; font-weight: 500; }
  .person__title { color: var(--text-light); font-size: 14px; margin-top: 6px; }

  .contact-list {
    position: absolute; left: 40px; top: 180px;
    list-style: none;
    font-size: 13px;
    color: var(--text-muted);
  }
  .contact-list li { display: flex; align-items: center; gap: 10px; margin-bottom: 9px; }
  .contact-list svg { width: 14px; height: 14px; flex: none; }
  .contact-list .address { align-items: flex-start; }
  .contact-list .address span { line-height: 1.45; }

  .web-band { position: absolute; right: 0; bottom: 0; width: 420px; height: 80px; }
  .web-band svg { position: absolute; inset: 0; }
  .web-band__url {
    position: absolute; right: 40px; bottom: 24px;
    font-size: 16px; font-weight: 500; color: var(--text-light);
  }
</style>
</head>
<body>
  <section class="card card--front" aria-label="Business card front">
    <div class="wordmark">
      <span class="wordmark__initials">RW</span>
      <span class="wordmark__name">FRAMEWELL</span>
    </div>
  </section>

  <section class="card card--back" aria-label="Business card back">
    <div class="person">
      <p class="person__name">Alex RW Marlow</p>
      <p class="person__title">Managing Director</p>
    </div>

    <ul class="contact-list">
      <li>
        <svg viewBox="0 0 14 14"><circle cx="7" cy="7" r="7" fill="var(--brand-blue)"/><path d="M4.5 3.8l1.3 1.3-.7.9c.5 1 1.3 1.8 2.3 2.3l.9-.7 1.3 1.3-.9 1c-2.5-.4-4.7-2.6-5.1-5.1z" fill="#fff"/></svg>
        <span>555-010-2468</span>
      </li>
      <li>
        <svg viewBox="0 0 14 14"><circle cx="7" cy="7" r="7" fill="var(--brand-blue)"/><rect x="3.5" y="4.5" width="7" height="5" fill="none" stroke="#fff" stroke-width="1"/><path d="M3.5 4.5L7 7.3 10.5 4.5" fill="none" stroke="#fff" stroke-width="1"/></svg>
        <span>alex@framewell.example</span>
      </li>
      <li class="address">
        <svg viewBox="0 0 14 14"><circle cx="7" cy="7" r="7" fill="var(--brand-blue)"/><path d="M7 3a2.6 2.6 0 0 1 2.6 2.6C9.6 7.6 7 11 7 11S4.4 7.6 4.4 5.6A2.6 2.6 0 0 1 7 3z" fill="#fff"/><circle cx="7" cy="5.6" r="1" fill="var(--brand-blue)"/></svg>
        <span>78 Sample Rd., Placeton,<br>Oregon, US 00000</span>
      </li>
    </ul>

    <div class="wordmark">
      <span class="wordmark__initials">RW</span>
      <span class="wordmark__name">FRAMEWELL</span>
    </div>

    <div class="web-band">
      <svg viewBox="0 0 420 80" preserveAspectRatio="none"><polygon points="60,0 420,0 420,80 0,80" fill="var(--brand-blue)"/></svg>
      <span class="web-band__url">www.framewell.example</span>
    </div>
  </section>
</body>
</html>
```